Awesome photographers card for an awesome new business

Double sided business card Black background and silver logo in middle on one side. Details on otherside. please keep it simple

Industry/Entity Type

Photographer

Contact Information for Business Card

Gerald Fenwick
0452817360
GeraldFenwickPhotography47@mailbox.test
www.GeraldFenwickPhotography.test.au
Instagram _Gerald_fenwick

Requirements
Must have
• My logo in Silver
• please use instagram logo instead of "Instagram"

```html
<!DOCTYPE html>
<html lang="en">
<head>
<meta charset="utf-8">
<title>Gerald Fenwick Photography – Business Card</title>
<link href="https://fonts.googleapis.com/css2?family=Open+Sans:wght@400;600;700&display=swap" rel="stylesheet">
<style>
  :root {
    --backdrop: #1e1e1e;
    --card-white: #f7f7f5;
    --card-black: #141414;
    --silver: #a9a9a9;
    --silver-light: #cfcfcf;
    --ink-grey: #5a5a5a;
    --text-light: #e6e6e6;
  }
  * { box-sizing: border-box; margin: 0; padding: 0; }
  html, body {
    width: 1200px; height: 900px; overflow: hidden;
    background: var(--backdrop);
    font-family: "Open Sans", Arial, sans-serif;
  }
  .canvas {
    position: relative; width: 1200px; height: 900px;
  }
  .card {
    position: absolute; left: 260px; width: 680px; height: 388px;
    box-shadow: 0 10px 30px rgba(0,0,0,.5);
  }
  .card--front { top: 40px; background: var(--card-white); }
  .card--back { top: 472px; background: var(--card-black); }

  .brand-seal {
    position: absolute; left: 50%; top: 48px; transform: translateX(-50%);
    width: 190px; height: 190px;
    display: flex; align-items: center; justify-content: center;
  }
  .brand-seal__ring {
    position: absolute; inset: 0;
    border: 3px solid var(--silver); border-radius: 50%;
  }
  .brand-seal__name {
    color: var(--silver); font-weight: 600; font-size: 19px;
    text-align: center; line-height: 1.3; letter-spacing: 2px;
    text-transform: uppercase;
  }
  .front-web {
    position: absolute; left: 0; right: 0; bottom: 62px; text-align: center;
    color: var(--ink-grey); font-size: 16px; letter-spacing: 3px;
  }

  .back-mark {
    position: absolute; left: 50px; top: 0; bottom: 0;
    display: flex; align-items: center;
    color: var(--silver); font-weight: 600; font-size: 44px;
    line-height: 1.1; width: 260px;
  }
  .contact {
    position: absolute; left: 380px; top: 140px;
    color: var(--text-light); font-size: 13px; line-height: 1.6;
  }
  .contact__name {
    font-weight: 700; font-size: 17px; text-transform: uppercase;
    margin-bottom: 10px; letter-spacing: .5px;
  }
  .contact__row { white-space: nowrap; }
  .contact__label { display: inline-block; width: 22px; }
  .contact__social-box {
    display: inline-block; width: 11px; height: 11px;
    background: var(--text-light); margin-right: 8px; vertical-align: -1px;
  }
</style>
</head>
<body>
<main class="canvas">
  <section class="card card--front">
    <div class="brand-seal">
      <span class="brand-seal__ring"></span>
      <span class="brand-seal__name">Gerald<br>Fenwick<br>Photography</span>
    </div>
    <p class="front-web">www.GeraldFenwickPhotography.test.au</p>
  </section>

  <section class="card card--back">
    <div class="back-mark">Gerald Fenwick</div>
    <div class="contact">
      <p class="contact__name">Gerald Fenwick</p>
      <p class="contact__row"><span class="contact__label">P:</span>0452817360</p>
      <p class="contact__row"><span class="contact__label">E:</span>GeraldFenwickPhotography47@mailbox.test</p>
      <p class="contact__row"><span class="contact__label">W:</span>www.GeraldFenwickPhotography.test.au</p>
      <p class="contact__row"><span class="contact__social-box"></span>_Gerald_fenwick</p>
    </div>
  </section>
</main>
</body>
</html>
```